Professional Package for CPA Firm

We would like a stationery design for our new CPA Firm based in Atlanta, GA called 'Vale 8'. We work with investors to help grow investments, tax free. We would like the design to have a professional/minimal look with a 'wow' factor. We need 9.5″ x 4.125″, 9x12, and 10x13 mailing envelopes, business cards, and a letterhead. We have a logo that is already complete. For the letterhead, we would like to have space to put credentials at the bottom of the page

Industry/Entity Type

CPA, Accounting

```html
<!DOCTYPE html>
<html lang="en">
<head>
<meta charset="UTF-8">
<title>Vale 8 – Business Card</title>
<link href="https://fonts.googleapis.com/css2?family=Lato:wght@400;700;900&display=swap" rel="stylesheet">
<style>
  :root {
    --bg: #8a8a8a;
    --paper: #ffffff;
    --navy: #0f2d47;
    --navy-deep: #062034;
    --navy-light: #14557e;
    --teal: #1ea5b8;
    --coral: #f0434b;
    --ink-grey: #4a4f55;
    --rule: #c9d3da;
  }
  * { margin: 0; padding: 0; box-sizing: border-box; }
  html, body {
    width: 1200px; height: 800px; overflow: hidden;
    background: var(--bg);
    font-family: "Lato", Arial, sans-serif;
  }
  .canvas {
    width: 1200px; height: 800px;
    display: flex; align-items: center; justify-content: center; gap: 60px;
  }
  .card {
    width: 520px; height: 298px;
    position: relative;
    border-bottom: 2px solid var(--teal);
    box-shadow: 0 10px 24px rgba(0,0,0,.25);
  }
  /* Front */
  .card-front { background: var(--paper); display: flex; }
  .brand-area {
    width: 262px; display: flex; align-items: center; justify-content: center; gap: 12px;
  }
  .brand-dot { width: 18px; height: 18px; border-radius: 50%; background: var(--coral); }
  .brand-name {
    font-weight: 900; font-size: 44px; color: var(--navy); letter-spacing: 1px;
  }
  .divider { width: 1px; background: var(--rule); margin: 70px 0; }
  .contact-area { padding: 56px 0 0 28px; color: var(--ink-grey); }
  .person-name {
    font-weight: 700; font-size: 21px; color: var(--navy); letter-spacing: .5px;
    text-transform: uppercase;
  }
  .person-role { font-size: 14px; color: var(--teal); margin-top: 2px; }
  .address { font-size: 12.5px; line-height: 1.45; margin-top: 14px; }
  .contact-list { list-style: none; margin-top: 10px; font-size: 12.5px; line-height: 1.55; }
  .contact-list li { display: flex; align-items: center; gap: 8px; }
  .contact-list svg { width: 11px; height: 11px; flex: none; }
  /* Back */
  .card-back { overflow: hidden; }
  .back-field {
    position: absolute; inset: 0;
    background: linear-gradient(200deg, var(--navy-deep) 0%, #0b3554 45%, var(--navy-light) 100%);
  }
  .back-name {
    position: absolute; right: 34px; bottom: 40px;
    font-weight: 900; font-size: 26px; color: var(--paper); letter-spacing: 1px;
  }
</style>
</head>
<body>
<main class="canvas">
  <section class="card card-front">
    <div class="brand-area">
      <span class="brand-dot"></span>
      <span class="brand-name">Vale 8</span>
    </div>
    <div class="divider"></div>
    <div class="contact-area">
      <h1 class="person-name">Daniel Reyes</h1>
      <p class="person-role">President</p>
      <p class="address">4120 Birchwood Lane<br>Marietta, Georgia 30062</p>
      <ul class="contact-list">
        <li>
          <svg viewBox="0 0 12 12"><path d="M2.5 1h2l1 3-1.3 1a6 6 0 0 0 2.8 2.8L8 6.5l3 1v2a1.5 1.5 0 0 1-1.5 1.5A8.5 8.5 0 0 1 1 2.5 1.5 1.5 0 0 1 2.5 1z" fill="var(--teal)"/></svg>
          404-555-0132
        </li>
        <li>
          <svg viewBox="0 0 12 12"><rect x="3" y="0.8" width="6" height="10.4" rx="1" fill="none" stroke="var(--teal)" stroke-width="1.3"/><circle cx="6" cy="9.2" r=".7" fill="var(--teal)"/></svg>
          404-555-0187
        </li>
        <li>
          <svg viewBox="0 0 12 12"><rect x=".8" y="2.3" width="10.4" height="7.4" rx="1" fill="var(--teal)"/><path d="M1.2 3l4.8 3.6L10.8 3" fill="none" stroke="#fff" stroke-width="1"/></svg>
          info@vale8.com
        </li>
        <li>
          <svg viewBox="0 0 12 12"><circle cx="6" cy="6" r="5" fill="var(--teal)"/><path d="M1 6h10M6 1c-2 2.7-2 7.3 0 10M6 1c2 2.7 2 7.3 0 10" fill="none" stroke="#fff" stroke-width=".8"/></svg>
          www.vale8.com
        </li>
      </ul>
    </div>
  </section>

  <section class="card card-back">
    <div class="back-field" role="img" aria-label="Decorative tonal pattern in deep navy and blue"></div>
    <span class="back-name">Vale 8</span>
  </section>
</main>
</body>
</html>
```